New Business Card Design Project

We require a business card design for Vexalund, a newly established Indian company.
Our focus is on the development, manufacturing, and export of a diverse array of pharmaceutical products on a global scale. The card should convey a professional appearance, as our primary markets are in Africa, China, and Southeast Asian nations.
We envision a two-sided business card, with the reverse side dedicated to a logo set against a solid color or an elegantly designed pattern. The corners should be rounded. We would appreciate seeing both horizontal and vertical design options. We trust the designer to utilize their expertise in creating this design.

The content for the business card is included in the attached Word file.

Target Market(s)

Our primary markets are in Africa, China, and Southeast Asian, Latin America, Maldives, Sri Lanka

Industry/Entity Type

Pharmaceutical Manufacturing and Export

Contact Information for Business Card

Colors

Designer to choose colors to be used in the design.

Requirements
Must have
• The reverse side of the business card features solely the logo along with the tagline, "Remedies of Life."
Should not have
• The logo should not exceed two instances, encompassing both the front and back sides of the card.

```html
<!DOCTYPE html>
<html lang="en">
<head>
<meta charset="utf-8">
<title>Vexalund Business Card</title>
<link rel="stylesheet" href="https://fonts.googleapis.com/css2?family=Montserrat:wght@400;500;700;800&display=swap">
<style>
  :root {
    --bg: #c9c8c5;
    --card-white: #ffffff;
    --brand-blue: #25a6e0;
    --brand-blue-deep: #1586c0;
    --brand-blue-light: #5cc5f2;
    --brand-coral: #ef5f4c;
    --ink: #1d1d1f;
  }
  * { box-sizing: border-box; margin: 0; padding: 0; }
  html, body {
    width: 1200px; height: 801px; overflow: hidden;
    background: var(--bg);
    font-family: "Montserrat", sans-serif;
  }
  .stage { position: relative; width: 1200px; height: 801px; }
  .card {
    position: absolute; top: 240px;
    width: 555px; height: 320px;
    border-radius: 12px; overflow: hidden;
    box-shadow: 0 10px 28px rgba(0,0,0,.18);
  }
  .card--front { left: 30px; background: var(--card-white); }
  .card--back { left: 615px; }

  .wave { position: absolute; inset: 0; width: 100%; height: 100%; }

  .brand {
    position: absolute; left: 30px; top: 140px;
    display: flex; align-items: center; gap: 10px;
  }
  .brand__dot {
    width: 20px; height: 20px; border-radius: 50%;
    background: var(--brand-coral); flex: none;
  }
  .brand__name {
    font-weight: 800; font-size: 34px; color: var(--brand-blue);
    letter-spacing: -0.5px; line-height: 1;
  }

  .divider {
    position: absolute; left: 262px; top: 40px;
    width: 1px; height: 170px; background: var(--brand-blue);
  }

  .details {
    position: absolute; left: 282px; top: 36px; width: 260px;
    color: var(--ink);
  }
  .details__name {
    font-weight: 800; font-size: 21px; color: var(--brand-blue);
    line-height: 1.15;
  }
  .details__role, .details__company { font-size: 13px; line-height: 1.35; }
  .contacts { list-style: none; margin-top: 14px; }
  .contacts li {
    display: flex; align-items: center; gap: 7px;
    font-size: 12px; line-height: 1.7;
  }
  .contacts svg { width: 12px; height: 12px; flex: none; }
  .address { margin-top: 12px; font-size: 12px; line-height: 1.45; font-style: normal; }

  .back-pattern {
    position: absolute; inset: 0;
    background: linear-gradient(135deg, var(--brand-blue-light) 0%, var(--brand-blue) 50%, var(--brand-blue-deep) 100%);
  }
  .back-brand {
    position: absolute; inset: 0;
    display: flex; flex-direction: column; align-items: center; justify-content: center;
    gap: 12px;
  }
  .back-brand__mark { display: flex; align-items: center; gap: 12px; }
  .back-brand__dot {
    width: 24px; height: 24px; border-radius: 50%;
    background: var(--brand-coral);
  }
  .back-brand__name {
    font-weight: 800; font-size: 44px; color: var(--card-white);
    letter-spacing: -0.5px; line-height: 1;
  }
  .back-brand__tagline {
    font-weight: 500; font-size: 15px; color: var(--card-white);
    letter-spacing: 3px; text-transform: uppercase;
  }
</style>
</head>
<body>
<main class="stage">
  <section class="card card--front" aria-label="Business card front">
    <svg class="wave" viewBox="0 0 555 320" preserveAspectRatio="none" aria-hidden="true">
      <path d="M0,282 C170,272 250,205 360,228 C440,245 500,262 555,250 L555,320 L0,320 Z" fill="var(--brand-coral)"/>
      <path d="M0,290 C170,280 250,213 360,236 C440,253 500,270 555,258 L555,320 L0,320 Z" fill="var(--card-white)"/>
      <path d="M0,294 C170,284 250,217 360,240 C440,257 500,274 555,262 L555,320 L0,320 Z" fill="var(--brand-blue)"/>
    </svg>

    <div class="brand">
      <span class="brand__dot"></span>
      <span class="brand__name">Vexalund</span>
    </div>

    <span class="divider"></span>

    <div class="details">
      <h1 class="details__name">Arjun K. Malhotra</h1>
      <p class="details__role">CEO</p>
      <p class="details__company">Vexalund</p>
      <ul class="contacts">
        <li>
          <svg viewBox="0 0 12 12" aria-hidden="true"><path d="M3 1 L5 3.5 L4 4.8 C4.7 6.2 5.8 7.3 7.2 8 L8.5 7 L11 9 L9.8 11 C5 10.5 1.5 7 1 2.2 Z" fill="var(--brand-blue)"/></svg>
          +919876543210
        </li>
        <li>
          <svg viewBox="0 0 12 12" aria-hidden="true"><rect x="0.5" y="2" width="11" height="8" rx="1" fill="var(--brand-coral)"/><path d="M1 2.5 L6 6.5 L11 2.5" stroke="#fff" fill="none"/></svg>
          amalhotra@vexalund.com
        </li>
        <li>
          <svg viewBox="0 0 12 12" aria-hidden="true"><circle cx="6" cy="6" r="5.5" fill="var(--brand-blue)"/><path d="M0.5 6 H11.5 M6 0.5 C3.5 3 3.5 9 6 11.5 M6 0.5 C8.5 3 8.5 9 6 11.5" stroke="#fff" stroke-width="0.8" fill="none"/></svg>
          www.vexalund.com
        </li>
      </ul>
      <address class="address">14, Kamal Nagar,<br>Nashik, 422001, India</address>
    </div>
  </section>

  <section class="card card--back" aria-label="Business card back">
    <div class="back-pattern" role="img" aria-label="Repeating embossed brand symbol pattern in shades of blue"></div>
    <div class="back-brand">
      <div class="back-brand__mark">
        <span class="back-brand__dot"></span>
        <span class="back-brand__name">Vexalund</span>
      </div>
      <p class="back-brand__tagline">Remedies of Life</p>
    </div>
  </section>
</main>
</body>
</html>
```